Business Cards for Internet Security Company

Awesome designers! This is the opportunity to help design cards for a forward thinking network security company. They use threat information gathered from peer groups to make intelligent decisions on what threats are relevant and which arent. ( not that you need this to do designs, but just so you know where they are coming from. ) :-)

We'd like to see a two side design and the deliverables will be in illustrator 4. The logo is attached and the logo colors are attached in the JPG and I've attached a an eps of the logo and icon

Security

```html
<!DOCTYPE html>
<html lang="en">
<head>
<meta charset="utf-8">
<title>Keltrane Business Cards</title>
<link href="https://fonts.googleapis.com/css2?family=Questrial&family=Open+Sans:wght@400;700&display=swap" rel="stylesheet">
<style>
  :root {
    --canvas-bg: #e9ebee;
    --card-white: #ffffff;
    --brand-blue: #2f5f88;
    --brand-navy: #0f2f52;
    --band-mid: #24507e;
    --band-light: #5f8fbc;
    --label-blue: #4d9be0;
    --faint-ring: #eef2f7;
    --text-white: #ffffff;
  }
  * { margin: 0; padding: 0; box-sizing: border-box; }
  html, body {
    width: 1200px; height: 913px; overflow: hidden;
    background: var(--canvas-bg);
  }
  .sheet {
    position: relative; width: 1200px; height: 913px;
    display: flex; align-items: center; justify-content: center; gap: 60px;
  }
  .card {
    position: relative; width: 500px; height: 286px;
    background: var(--card-white); overflow: hidden;
    box-shadow: 0 6px 18px rgba(0,0,0,.18);
  }
  .brand {
    display: flex; align-items: center; gap: 14px;
    font-family: "Questrial", sans-serif; color: var(--brand-blue);
    position: absolute;
  }
  .brand-dot { border-radius: 50%; background: var(--brand-blue); flex: none; }

  /* front */
  .card-front .faint-ring {
    position: absolute; left: 40px; top: 40px; width: 230px; height: 230px;
    border-radius: 50%; border: 30px solid var(--faint-ring);
  }
  .card-front .brand { left: 52px; top: 104px; font-size: 66px; letter-spacing: 1px; }
  .card-front .brand-dot { width: 44px; height: 44px; }

  /* back */
  .card-back .brand { left: 48px; top: 48px; font-size: 52px; letter-spacing: 1px; }
  .card-back .brand-dot { width: 38px; height: 38px; }
  .card-back .band { position: absolute; inset: 0; }
  .contact {
    position: absolute; left: 0; right: 0; bottom: 0; height: 122px;
    font-family: "Open Sans", sans-serif; color: var(--text-white);
  }
  .holder-name {
    position: absolute; left: 24px; top: 12px;
    font-weight: 700; font-size: 17px;
  }
  .details {
    position: absolute; left: 150px; top: 14px; right: 16px;
    font-size: 11.5px; line-height: 24px;
  }
  .details .label { color: var(--label-blue); }
</style>
</head>
<body>
<main class="sheet">
  <section class="card card-front" aria-label="Card front">
    <div class="faint-ring"></div>
    <div class="brand"><span class="brand-dot"></span><span class="brand-name">Keltrane</span></div>
  </section>

  <section class="card card-back" aria-label="Card back">
    <svg class="band" width="500" height="286" viewBox="0 0 500 286" aria-hidden="true">
      <defs>
        <linearGradient id="bandFill" x1="0" y1="1" x2="1" y2="0">
          <stop offset="0" stop-color="#0f2f52"/>
          <stop offset="0.55" stop-color="#24507e"/>
          <stop offset="1" stop-color="#3c6e9f"/>
        </linearGradient>
      </defs>
      <polygon points="260,120 500,64 500,140 260,164" fill="#5f8fbc"/>
      <polygon points="0,164 500,140 500,286 0,286" fill="url(#bandFill)"/>
      <polygon points="70,164 86,164 78,174" fill="#ffffff"/>
      <polygon points="410,106 426,104 419,114" fill="#ffffff"/>
    </svg>
    <div class="brand"><span class="brand-dot"></span><span class="brand-name">Keltrane</span></div>
    <div class="contact">
      <p class="holder-name">Your Name</p>
      <div class="details">
        <p><span class="label">Add.:</span> Your Communication Address in just two line</p>
        <p><span class="label">Ph.:</span> (000) 000-000-000</p>
        <p><span class="label">Email:</span> yourname@yourwebsite.com <span class="label">| Web.:</span> www.yourwebsite.com</p>
      </div>
    </div>
  </section>
</main>
</body>
</html>
```